Investment company needing business card

We are wanting a business card which looks sharp and easy on the eye. We are thinking of having a business card with the logo embossed on it, to really make it stand out. We will only have a small amount of information of the business card, person's name, position, email address and phone number

Contact Information for Business Card

Danielle Frost
Executive Assistant
+64 21 473 5162
danielf@harwickpartners.co.nz

Requirements
Must have
• Embossed logo
Should not have
• Not to be busy

```html
<!DOCTYPE html>
<html lang="en">
<head>
<meta charset="utf-8">
<title>Harwick Partners – Business Card</title>
<link rel="stylesheet" href="https://fonts.googleapis.com/css2?family=Lato:wght@400;700;900&display=swap">
<style>
  :root {
    --stage: #2e2b29;
    --card-black: #111111;
    --card-charcoal: #1f1f20;
    --emboss: #8c8c8c;
    --green: #1fb574;
    --white: #ffffff;
    --text-light: #e6e6e6;
  }
  * { margin: 0; padding: 0; box-sizing: border-box; }
  html, body { width: 1200px; height: 780px; overflow: hidden; }
  body {
    background: var(--stage);
    font-family: "Lato", sans-serif;
    position: relative;
  }
  .card {
    position: absolute;
    width: 520px;
    height: 297px;
    border-radius: 4px;
    overflow: hidden;
    box-shadow: 0 14px 30px rgba(0,0,0,.45);
  }
  .card-back {
    left: 50px; top: 120px;
    background: var(--card-black);
    display: flex; align-items: center; justify-content: center;
  }
  .card-front {
    left: 630px; top: 360px;
    background: var(--card-charcoal);
  }
  .brand {
    display: flex; align-items: center; gap: 12px;
    font-weight: 900;
    letter-spacing: 2px;
    text-transform: uppercase;
    line-height: 1;
  }
  .brand-mark { width: 22px; height: 22px; }
  .card-back .brand { color: var(--emboss); font-size: 30px; }
  .card-back .brand-mark { background: var(--emboss); }
  .card-front .brand {
    position: absolute; left: 30px; top: 38px;
    color: var(--green); font-size: 28px;
  }
  .card-front .brand-mark { background: var(--green); }
  .contact {
    position: absolute; left: 30px; top: 126px;
    color: var(--text-light);
  }
  .contact-name { color: var(--green); font-weight: 700; font-size: 17px; }
  .contact-role { font-size: 14px; margin-bottom: 10px; }
  .contact-line { display: flex; align-items: center; gap: 8px; font-size: 14px; margin-top: 4px; }
  .contact-line svg { width: 11px; height: 11px; flex: none; }
  .accent-band { position: absolute; left: 0; bottom: 0; width: 520px; height: 297px; }
</style>
</head>
<body>
  <section class="card card-back" aria-label="Card back">
    <div class="brand"><span class="brand-mark"></span>Harwick Partners</div>
  </section>

  <section class="card card-front" aria-label="Card front">
    <svg class="accent-band" viewBox="0 0 520 297" aria-hidden="true">
      <polygon points="0,214 330,258 330,262 0,218" fill="var(--white)"/>
      <polygon points="0,226 300,266 320,260 520,260 520,297 0,297" fill="var(--green)"/>
    </svg>
    <div class="brand"><span class="brand-mark"></span>Harwick Partners</div>
    <div class="contact">
      <p class="contact-name">Danielle Frost</p>
      <p class="contact-role">Executive Assistant</p>
      <p class="contact-line">
        <svg viewBox="0 0 12 12"><rect x="1" y="1" width="10" height="10" fill="none" stroke="var(--green)" stroke-width="1.4"/></svg>
        +64 21 473 5162
      </p>
      <p class="contact-line">
        <svg viewBox="0 0 12 12"><rect x="1" y="2" width="10" height="8" fill="var(--green)"/><polyline points="1,2 6,7 11,2" fill="none" stroke="var(--card-charcoal)" stroke-width="1.2"/></svg>
        danielf@harwickpartners.co.nz
      </p>
    </div>
  </section>
</body>
</html>
```